Wealth Education Business Needs Sharp Business Card Design

We need a business card design for a recently launched investor education business called Harbor Crest.

The final design should promote security, empowerment, self improvement and financial gain. The card will ideally promote the stature of the business.

For more information and colours please visit harborcrest.com.au

Target Market(s)

Corporate executives and high net worth individuals

Industry/Entity Type

Education

Contact Information for Business Card

```html
<!DOCTYPE html>
<html lang="en">
<head>
<meta charset="UTF-8">
<title>Harbor Crest – Business Card</title>
<link href="https://fonts.googleapis.com/css2?family=Lato:wght@400;700&display=swap" rel="stylesheet">
<style>
  :root {
    --backdrop: #e4e4e4;
    --card-white: #fbfbfb;
    --ink: #1f1f1f;
    --wordmark-grey: #3b3b3b;
    --teal: #17706b;
    --band-teal: #0f7a74;
    --blue-light: #3399d8;
    --blue-deep: #1b7fc3;
    --white: #ffffff;
  }
  * { margin: 0; padding: 0; box-sizing: border-box; }
  html, body {
    width: 1200px; height: 720px; overflow: hidden;
    background: var(--backdrop);
    font-family: "Lato", sans-serif;
  }
  .canvas { position: relative; width: 1200px; height: 720px; }

  .card {
    position: absolute; top: 241px;
    width: 419px; height: 240px;
    border-radius: 14px; overflow: hidden;
  }
  .card-front { left: 148px; background: var(--card-white); }
  .card-back {
    left: 633px;
    background: linear-gradient(135deg, var(--blue-light), var(--blue-deep));
  }

  .front-wordmark {
    position: absolute; left: 21px; top: 30px;
    font-size: 25px; font-weight: 400; letter-spacing: 4px;
    color: var(--wordmark-grey);
  }
  .holder-name {
    position: absolute; left: 19px; top: 95px;
    font-size: 16px; font-weight: 700; color: var(--teal);
  }
  .holder-role {
    position: absolute; left: 19px; top: 115px;
    font-size: 11px; font-weight: 700; color: var(--ink);
  }
  .contact-list {
    position: absolute; left: 17px; top: 147px;
    list-style: none;
  }
  .contact-list li {
    display: flex; align-items: center; gap: 5px;
    font-size: 12px; line-height: 14.5px; color: var(--ink);
  }
  .contact-list svg { width: 11px; height: 11px; fill: var(--wordmark-grey); flex: none; }
  .office-address {
    position: absolute; right: 22px; top: 170px;
    text-align: right; font-size: 12px; line-height: 15px;
    font-style: normal; color: var(--ink);
  }
  .front-band { position: absolute; left: 0; bottom: 0; width: 419px; height: 30px; }

  .back-wordmark {
    position: absolute; left: 0; right: 0; top: 101px;
    text-align: center;
    font-size: 33px; font-weight: 400; letter-spacing: 6px;
    color: var(--white);
  }
  .back-url {
    position: absolute; left: 0; right: 0; top: 210px;
    text-align: center; font-size: 12px; color: var(--white);
  }
</style>
</head>
<body>
<main class="canvas">
  <section class="card card-front">
    <div class="front-wordmark">HARBOR CREST</div>
    <div class="holder-name">Marcus Hale</div>
    <div class="holder-role">Director</div>
    <ul class="contact-list">
      <li>
        <svg viewBox="0 0 12 12" aria-hidden="true"><path d="M1 4.5C1 2.5 3 1.5 6 1.5s5 1 5 3l-2 .6-.6-1.6H3.6L3 5.1zM2.5 6h7l1 4.5h-9z"/></svg>
        1300 555 148
      </li>
      <li>
        <svg viewBox="0 0 12 12" aria-hidden="true"><path d="M3.5 0.5h5a1 1 0 0 1 1 1v9a1 1 0 0 1-1 1h-5a1 1 0 0 1-1-1v-9a1 1 0 0 1 1-1zm.4 1.5v7h4.2V2z"/></svg>
        +613 5550 2716
      </li>
      <li>
        <svg viewBox="0 0 12 12" aria-hidden="true"><path d="M0.5 2.5h11v7h-11zM1.5 3.3 6 6.6l4.5-3.3z" fill-rule="evenodd"/></svg>
        support@harborcrest.com.au
      </li>
      <li>
        <svg viewBox="0 0 12 12" aria-hidden="true"><path d="M6 .5a5.5 5.5 0 1 0 0 11A5.5 5.5 0 0 0 6 .5zm0 1.2c.8.8 1.3 2 1.5 3.4h-3C4.7 3.7 5.2 2.5 6 1.7zM1.8 6.9h1.9c.1 1.2.5 2.3 1 3.1A4.3 4.3 0 0 1 1.8 6.9zm0-1.8a4.3 4.3 0 0 1 2.9-3.1c-.5.8-.9 1.9-1 3.1zm2.7 1.8h3c-.2 1.4-.7 2.6-1.5 3.4-.8-.8-1.3-2-1.5-3.4zm2.8 3.1c.5-.8.9-1.9 1-3.1h1.9a4.3 4.3 0 0 1-2.9 3.1zm1-4.9c-.1-1.2-.5-2.3-1-3.1a4.3 4.3 0 0 1 2.9 3.1z"/></svg>
        www.harborcrest.com.au
      </li>
    </ul>
    <address class="office-address">
      Level 4, 52 Harbour Row<br>
      Southbank VIC 3006
    </address>
    <svg class="front-band" viewBox="0 0 419 30" preserveAspectRatio="none" aria-hidden="true">
      <path d="M0 4 Q170 22 419 14 L419 30 L0 30 Z" fill="var(--band-teal)"/>
    </svg>
  </section>

  <section class="card card-back">
    <div class="back-wordmark">HARBOR CREST</div>
    <div class="back-url">www.harborcrest.com.au</div>
  </section>
</main>
</body>
</html>
```